Best local air conditioning and heating contractor

We need a website design for a new company in Tampa Bay called the Coastal Breeze Cooling Company. We provide superior services for residential and commercial properties as well as maintenance and installing HVAC systems. We also want to sell equipment, parts and filter on the website as well. We want it easy to use for customers. Rich with content and keywords for our area.

Target Market(s)

homeowners in Tampa Bay

Industry/Entity Type

HVAC air conditioning and heating

Coding

Coded - Design and coding required

Number of Pages Required

5+ page

Font styles to use
Sans Serif

Requirements
Nice to have
• would like the colors to be same as logo

```html
<!DOCTYPE html>
<html lang="en">
<head>
<meta charset="utf-8">
<title>Coastal Breeze Cooling Company</title>
<link href="https://fonts.googleapis.com/css2?family=Audiowide&family=Roboto:wght@400;500;700&family=Poppins:wght@400;500&family=Tinos:wght@700&display=swap" rel="stylesheet">
<style>
:root{
  --navy:#23377a;
  --navy-dark:#1c2c66;
  --red:#e1232b;
  --red-dark:#c81d24;
  --lav:#eceff7;
  --text:#333;
  --white:#fff;
}
*{margin:0;padding:0;box-sizing:border-box}
html,body{width:1200px;height:4228px;overflow:hidden;background:#fff}
body{position:relative;font-family:'Roboto',sans-serif;color:var(--text)}
.abs{position:absolute}
.display{font-family:'Audiowide',sans-serif;text-transform:uppercase;letter-spacing:1px}
.brand{font-family:'Roboto',sans-serif;font-weight:700;color:var(--navy);line-height:1.05;text-transform:uppercase}

/* header */
.topbar{top:0;left:0;width:1200px;height:94px;border-top:3px solid var(--red)}
.top-info{display:flex;align-items:center;gap:14px}
.icon-circle{width:42px;height:42px;border-radius:50%;background:var(--red);display:flex;align-items:center;justify-content:center}
.top-info .label{font-family:'Audiowide',sans-serif;text-transform:uppercase;color:var(--navy);font-size:14px;letter-spacing:1px}
.top-info .value{font-size:14px;color:#333;margin-top:4px}

.nav{top:94px;left:0;width:1200px;height:54px;background:var(--navy)}
.nav-red{top:94px;left:818px;width:382px;height:54px;background:var(--red);clip-path:polygon(22px 0,100% 0,100% 100%,0 100%)}
.nav-links{top:111px;left:105px;display:flex;font-size:14px;color:#fff}
.nav-links span{margin-right:38px}
.nav-links .active{text-decoration:underline}
.search{top:108px;left:871px;width:262px;height:28px;border-bottom:1px solid #fff;color:#fff;font-size:14px;display:flex;align-items:center;gap:8px}

/* hero */
.hero{top:148px;left:0;width:1200px;height:599px;
  background:
    radial-gradient(ellipse 260px 60px at 550px 30px,rgba(255,255,255,.9),rgba(255,255,255,0) 100%),
    radial-gradient(ellipse 420px 150px at 360px 420px,rgba(70,84,98,.85),rgba(70,84,98,0) 100%),
    radial-gradient(ellipse 160px 200px at 320px 370px,rgba(190,210,200,.6),rgba(190,210,200,0) 100%),
    radial-gradient(ellipse 260px 90px at 900px 560px,rgba(196,160,120,.55),rgba(196,160,120,0) 100%),
    linear-gradient(100deg,#a8b4bb 0%,#c3cccf 40%,#ccd4d6 70%,#d0d7d8 100%)}
.hero-text{top:300px;right:104px;text-align:right}
.hero-text .kicker{font-size:18px;color:var(--navy)}
.hero-text h1{font-size:42px;color:var(--red);margin-top:8px;line-height:1}
.hero-text h2{font-size:21px;color:var(--navy);margin-top:8px}
.hero-text p{font-size:14px;line-height:26px;color:#333;margin-top:12px}
.btn{display:inline-block;background:var(--red);color:#fff;font-family:'Audiowide',sans-serif;text-transform:uppercase;border-radius:20px;text-align:center;letter-spacing:1px}
.hero-btn{top:515px;left:815px;width:280px;height:40px;line-height:40px;font-size:14px}
.dot{width:20px;height:20px;border-radius:50%;background:#7b8187}
.dot.on{background:var(--red)}

/* about */
.about-bar{top:837px;left:103px;width:4px;height:148px;background:var(--red)}
.about-head{top:840px;left:123px}
.about-head .kicker{font-size:16px;color:var(--navy)}
.about-head h2{font-size:27px;line-height:41px;margin-top:6px}
.about-head h2 .r{color:var(--red)}
.about-head h2 .b{color:var(--navy)}
.about-body{top:1000px;left:103px;width:460px;font-size:14px;line-height:25px;color:#333}
.about-body p+p{margin-top:8px}
.about-btn{top:1219px;left:103px;width:168px;height:37px;line-height:37px;font-size:14px}
.photo-big{top:842px;left:685px;width:410px;height:410px;border-radius:50%;
  background:
    radial-gradient(ellipse 120px 80px at 300px 110px,rgba(40,90,190,.75),rgba(40,90,190,0) 100%),
    radial-gradient(ellipse 110px 180px at 300px 260px,rgba(245,245,245,.9),rgba(245,245,245,0) 100%),
    radial-gradient(ellipse 120px 90px at 130px 130px,rgba(255,255,255,.95),rgba(255,255,255,0) 100%),
    linear-gradient(135deg,#eef0f2,#d3d7dc 55%,#a9b0b9)}
.photo-small{top:1063px;left:669px;width:230px;height:230px;border-radius:50%;border:7px solid #fff;box-shadow:0 4px 14px rgba(0,0,0,.25);
  background:
    radial-gradient(ellipse 70px 40px at 110px 40px,rgba(210,220,232,.9),rgba(210,220,232,0) 100%),
    linear-gradient(180deg,#b9c7d6 0%,#4b6fb3 40%,#1f46a0 75%,#17357a 100%)}

/* services */
.svc-band{top:1382px;left:0;width:1200px;height:484px;
  background:
    radial-gradient(ellipse 220px 200px at 1030px 150px,rgba(110,125,170,.45),rgba(110,125,170,0) 100%),
    radial-gradient(ellipse 260px 160px at 350px 190px,rgba(100,115,165,.35),rgba(100,115,165,0) 100%),
    linear-gradient(180deg,#2f4285,#2a3c7e)}
.svc-light{top:1866px;left:0;width:1200px;height:825px;background:var(--lav)}
.center{left:0;width:1200px;text-align:center}
.svc-kicker{top:1460px;font-size:16px;color:#fff}
.svc-title{top:1490px;font-size:24px;color:#fff}
.svc-sub{top:1535px;font-size:16px;color:#fff}
.card{top:1597px;width:302px;height:530px;background:#fafafa;box-shadow:0 2px 6px rgba(0,0,0,.12);text-align:center}
.card-img{height:269px;width:100%}
.card-icon{position:absolute;top:207px;left:89px;width:124px;height:124px;border-radius:50%;background:#fff;display:flex;align-items:center;justify-content:center}
.card-icon.dashed{border-bottom:1px dashed var(--navy)}
.card-icon.filled{background:var(--red)}
.card h3{font-family:'Tinos',serif;font-size:20px;color:#222;margin-top:82px}
.card p{font-size:14px;line-height:26px;color:#333;margin:14px 24px 0}
.card .more{font-family:'Audiowide',sans-serif;text-transform:uppercase;color:var(--red);font-size:14px;text-decoration:underline;margin-top:18px;display:block;letter-spacing:1px}

/* reviews */
.rev-kicker{top:2221px;font-size:16px;color:var(--navy)}
.rev-title{top:2250px;font-size:24px;color:var(--red)}
.avatar{top:2318px;left:560px;width:80px;height:80px;border-radius:50%;background:linear-gradient(160deg,#e3e6ea,#8f9aa6 60%,#4d5866)}
.rev-text{top:2414px;left:175px;width:850px;text-align:center;font-size:14px;line-height:24px;color:#333}
.rev-name{top:2528px;font-size:24px;color:#333;font-family:'Poppins',sans-serif}

/* locations */
.map{top:2770px;left:103px;width:410px;height:410px;border-radius:50%;
  background:
    radial-gradient(ellipse 50px 22px at 90px 70px,rgba(180,220,180,.8),rgba(180,220,180,0) 100%),
    radial-gradient(ellipse 40px 18px at 300px 70px,rgba(160,210,230,.8),rgba(160,210,230,0) 100%),
    radial-gradient(circle at 45% 45%,#f5f2e6,#ece7d5)}
.loc-bar{top:2770px;left:643px;width:4px;height:69px;background:var(--red)}
.loc-head{top:2771px;left:661px}
.loc-head .kicker{font-size:16px;color:var(--navy)}
.loc-head h2{font-size:29px;color:var(--red);margin-top:6px}
.loc-text{top:2858px;left:643px;width:420px;font-size:14px;line-height:25px;color:#333}
.loc-list{top:2918px;left:643px;display:grid;grid-template-columns:160px 160px;row-gap:11px;font-size:14px;color:#333}
.loc-list div{display:flex;align-items:center;gap:6px;height:22px}
.loc-btn{top:3131px;left:643px;width:168px;height:36px;line-height:36px;font-size:14px}

/* contact */
.contact{top:3233px;left:0;width:1200px;height:599px;
  background:
    radial-gradient(ellipse 220px 160px at 850px 260px,rgba(240,120,120,.35),rgba(240,120,120,0) 100%),
    radial-gradient(ellipse 300px 120px at 600px 560px,rgba(150,20,25,.35),rgba(150,20,25,0) 100%),
    linear-gradient(180deg,#d9252c,#e2313a 50%,#d3222a)}
.con-kicker{top:3358px;font-size:16px;color:#fff}
.con-title{top:3390px;font-size:27px;color:#fff}
.field{background:#fff;font-family:'Poppins',sans-serif;font-size:16px;color:#444;padding:0 20px;display:flex;align-items:center}
.field.msg{align-items:flex-start;padding-top:20px}
.submit{top:3736px;left:538px;width:123px;height:37px;line-height:33px;border:2px solid #fff;border-radius:20px;color:#fff;font-family:'Audiowide',sans-serif;text-transform:uppercase;font-size:14px;text-align:center;letter-spacing:1px}

/* footer */
.foot-h{font-family:'Audiowide',sans-serif;text-transform:uppercase;font-size:14px;color:#222;letter-spacing:1px}
.foot-h::after{content:"";display:block;width:42px;height:3px;background:var(--red);margin-top:14px}
.foot-links{font-family:'Poppins',sans-serif;font-size:14px;color:#333;line-height:29.5px}
.contact-item{display:flex;align-items:center;gap:10px;font-family:'Tinos',serif;font-size:16px;color:#222}
.ic-navy{width:26px;height:26px;border-radius:50%;background:var(--navy);display:flex;align-items:center;justify-content:center}
.foot-small{font-family:'Poppins',sans-serif;font-size:13px;color:#333;line-height:22px}
.copy{top:4186px;font-family:'Poppins',sans-serif;font-size:12px;color:#333}
.copy a{color:var(--red);text-decoration:underline}
</style>
</head>
<body>

<header class="abs topbar">
  <div class="abs" style="top:22px;left:103px;display:flex;align-items:center;gap:8px">
    <div style="width:14px;height:14px;background:var(--red)"></div>
    <div class="brand" style="font-size:17px">Coastal Breeze<br><span style="font-size:12px">Cooling Company</span></div>
  </div>
  <div class="abs top-info" style="top:25px;left:537px">
    <div class="icon-circle">
      <svg width="22" height="22" viewBox="0 0 24 24" fill="none" stroke="#fff" stroke-width="2.2"><circle cx="12" cy="12" r="9"/><path d="M12 7v5l3 2"/></svg>
    </div>
    <div><div class="label">24 Emergency Services :</div><div class="value">Monday - Saturday</div></div>
  </div>
  <div class="abs top-info" style="top:25px;left:927px">
    <div class="icon-circle">
      <svg width="20" height="20" viewBox="0 0 24 24" fill="#fff"><path d="M6.6 10.8a15 15 0 0 0 6.6 6.6l2.2-2.2c.3-.3.7-.4 1-.2 1.1.4 2.3.6 3.6.6.6 0 1 .4 1 1V20c0 .6-.4 1-1 1A17 17 0 0 1 3 4c0-.6.4-1 1-1h3.5c.6 0 1 .4 1 1 0 1.3.2 2.5.6 3.6.1.3 0 .7-.2 1z"/></svg>
    </div>
    <div><div class="label">Call Us :</div><div class="value">+1 813 555 0142</div></div>
  </div>
</header>

<nav>
  <div class="abs nav"></div>
  <div class="abs nav-red"></div>
  <div class="abs nav-links">
    <span class="active">Home</span><span>About Us</span><span>Our Services</span><span>Testimonials</span><span>Contact Us</span><span>Request Service</span>
  </div>
  <div class="abs search">
    <svg width="14" height="14" viewBox="0 0 24 24" fill="none" stroke="#fff" stroke-width="3"><circle cx="10" cy="10" r="7"/><path d="M15 15l6 6"/></svg>
    Search....
  </div>
</nav>

<section>
  <div class="abs hero" role="img" aria-label="Woman relaxing on a grey sofa using a remote to control a wall-mounted air conditioner"></div>
  <div class="abs hero-text">
    <div class="display kicker">Welcome to</div>
    <h1 class="display">Coastal Breeze</h1>
    <h2 class="display">Cooling Company</h2>
    <p>Lorem ipsum dolor sit amet, consectetur adipiscing elit, sed do<br>eiusmod tempor incididunt ut labore et dolore magna aliqua.<br>Quis ipsum suspendisse ultrices gravida.</p>
  </div>
  <div class="abs btn hero-btn">Book an Appointment</div>
  <div class="abs dot" style="top:640px;left:988px"></div>
  <div class="abs dot" style="top:640px;left:1017px"></div>
  <div class="abs dot" style="top:640px;left:1047px"></div>
  <div class="abs dot on" style="top:640px;left:1075px"></div>
</section>

<section>
  <div class="abs about-bar"></div>
  <div class="abs about-head">
    <div class="display kicker">About</div>
    <h2 class="display"><span class="r">Coastal Breeze</span><br><span class="b">Cooling</span><br><span class="b">Company</span></h2>
  </div>
  <div class="abs about-body">
    <p>Lorem ipsum dolor sit amet, consectetur adipiscing elit, sed do eiusmod tempor incididunt ut labore et dolore magna aliqua. Quis ipsum suspendisse ultrices gravida. Risus commodo viverra maecenas accumsan lacus vel facilisis.</p>
    <p>Sed ut perspiciatis unde omnis iste natus error sit voluptatem accusantium doloremque laudantium, totam rem aperiam, eaque ipsa quae ab illo inventore veritatis et quasi architecto beatae vitae dicta sunt explicabo. Nemo enim ipsam voluptatem quia voluptas sit.</p>
  </div>
  <div class="abs btn about-btn">Read More</div>
  <div class="abs photo-big" role="img" aria-label="Technician in a blue hard hat servicing an indoor air conditioning unit"></div>
  <div class="abs photo-small" role="img" aria-label="Two technicians in blue uniforms and hard hats"></div>
</section>

<section>
  <div class="abs svc-band" role="img" aria-label="Rooftop condenser units in a blue tint"></div>
  <div class="abs svc-light"></div>
  <div class="abs center display svc-kicker">What we do</div>
  <div class="abs center display svc-title">Superior Services</div>
  <div class="abs center svc-sub">Residential and Commercial properties</div>

  <div class="abs card" style="left:130px">
    <div class="card-img" role="img" aria-label="Technician repairing an HVAC unit" style="background:linear-gradient(135deg,#d4d7db,#9aa0a8 50%,#b4313a 80%,#1f2a44)"></div>
    <div class="card-icon dashed">
      <svg width="70" height="56" viewBox="0 0 70 56" fill="none" stroke="var(--navy)" stroke-width="2.5"><rect x="4" y="4" width="62" height="22" rx="3"/><path d="M10 18h50"/><circle cx="24" cy="38" r="13"/><path d="M24 28v20M15 33l18 10M15 43l18-10"/><path d="M46 36c3 3-3 6 0 10M54 36c3 3-3 6 0 10M62 36c3 3-3 6 0 10"/></svg>
    </div>
    <h3>HVAC</h3>
    <p>Lorem ipsum dolor sit amet,tur elit, sed dousmod tempor incididunt ut labore et dolore magna aliqua.</p>
    <span class="more">Read More</span>
  </div>

  <div class="abs card" style="left:448px">
    <div class="card-img" role="img" aria-label="Technicians inspecting outdoor condenser units with a tablet" style="background:linear-gradient(135deg,#f0f1f3,#c6cad0 55%,#8d96a1)"></div>
    <div class="card-icon filled">
      <svg width="60" height="56" viewBox="0 0 60 56" fill="none" stroke="#fff" stroke-width="2.5"><rect x="6" y="6" width="42" height="26" rx="3"/><path d="M12 14h20M12 22h14"/><path d="M28 38l10-10 8 8-10 10zM44 34l10 10"/><path d="M14 38v10h14"/></svg>
    </div>
    <h3>Maintenance</h3>
    <p>Lorem ipsum dolor sit amet,tur elit, sed dousmod tempor incididunt ut labore et dolore magna aliqua.</p>
    <span class="more">Read More</span>
  </div>

  <div class="abs card" style="left:768px">
    <div class="card-img" role="img" aria-label="Electrician installing wiring in an HVAC control panel" style="background:linear-gradient(135deg,#f1f2f4,#c9cdd2 50%,#c44a4f 70%,#3a4250)"></div>
    <div class="card-icon dashed">
      <svg width="56" height="56" viewBox="0 0 56 56" fill="none" stroke="var(--navy)" stroke-width="2.5"><path d="M14 8c-5 5 5 9 0 14s5 9 0 14M26 8c-5 5 5 9 0 14s5 9 0 14M38 8c-5 5 5 9 0 14s5 9 0 14"/><path d="M6 44h44M10 50h36"/></svg>
    </div>
    <h3>Installing HVAC systems</h3>
    <p>Lorem ipsum dolor sit amet,tur elit, sed dousmod tempor incididunt ut labore et dolore magna aliqua.</p>
    <span class="more">Read More</span>
  </div>
</section>

<section>
  <div class="abs center display rev-kicker">What our clients says</div>
  <div class="abs center display rev-title">Reviews</div>
  <div class="abs avatar" role="img" aria-label="Customer portrait"></div>
  <p class="abs rev-text">Lorem ipsum dolor sit amet, consectetur adipiscing elit, sed do eiusmod tempor incididunt ut labore et dolore magna aliqua. Quis ipsum suspendisse ultrices gravida. Risus commodo viverra maecenas accumsan lacus vel facilisis. Sed ut perspiciatis unde omnis iste natus error sit voluptatem accusantium doloremque laudantium, totam rem aperiam, eaque ipsa quae ab illo inventore veritatis et quasi architecto beatae vitae dicta sunt explicabo.</p>
  <div class="abs center rev-name">-Mara Ellison</div>
  <div class="abs dot on" style="top:2588px;left:559px"></div>
  <div class="abs dot" style="top:2588px;left:589px"></div>
  <div class="abs dot" style="top:2588px;left:620px"></div>
</section>

<section>
  <div class="abs map" role="img" aria-label="Map of the Tampa Bay service area"></div>
  <div class="abs loc-bar"></div>
  <div class="abs loc-head">
    <div class="display kicker">Locations</div>
    <h2 class="display">Areas we served</h2>
  </div>
  <p class="abs loc-text">Lorem ipsum dolor sit amet, consectetur adipiscing elit, sed do eiusmod tempor incididunt ut labore et dolore magna aliqua.</p>
  <div class="abs loc-list">
    <div><svg width="14" height="14" viewBox="0 0 16 16"><circle cx="8" cy="8" r="8" fill="#222"/><path d="M5 8h6M8 5l3 3-3 3" stroke="#fff" stroke-width="1.8" fill="none"/></svg>Lorem ipsum dolor</div>
    <div><svg width="14" height="14" viewBox="0 0 16 16"><circle cx="8" cy="8" r="8" fill="#222"/><path d="M5 8h6M8 5l3 3-3 3" stroke="#fff" stroke-width="1.8" fill="none"/></svg>Lorem ipsum dolor</div>
    <div><svg width="14" height="14" viewBox="0 0 16 16"><circle cx="8" cy="8" r="8" fill="#222"/><path d="M5 8h6M8 5l3 3-3 3" stroke="#fff" stroke-width="1.8" fill="none"/></svg>Lorem ipsum dolor</div>
    <div><svg width="14" height="14" viewBox="0 0 16 16"><circle cx="8" cy="8" r="8" fill="#222"/><path d="M5 8h6M8 5l3 3-3 3" stroke="#fff" stroke-width="1.8" fill="none"/></svg>Lorem ipsum dolor</div>
    <div><svg width="14" height="14" viewBox="0 0 16 16"><circle cx="8" cy="8" r="8" fill="#222"/><path d="M5 8h6M8 5l3 3-3 3" stroke="#fff" stroke-width="1.8" fill="none"/></svg>Lorem ipsum dolor</div>
    <div><svg width="14" height="14" viewBox="0 0 16 16"><circle cx="8" cy="8" r="8" fill="#222"/><path d="M5 8h6M8 5l3 3-3 3" stroke="#fff" stroke-width="1.8" fill="none"/></svg>Lorem ipsum dolor</div>
    <div><svg width="14" height="14" viewBox="0 0 16 16"><circle cx="8" cy="8" r="8" fill="#222"/><path d="M5 8h6M8 5l3 3-3 3" stroke="#fff" stroke-width="1.8" fill="none"/></svg>Lorem ipsum dolor</div>
    <div><svg width="14" height="14" viewBox="0 0 16 16"><circle cx="8" cy="8" r="8" fill="#222"/><path d="M5 8h6M8 5l3 3-3 3" stroke="#fff" stroke-width="1.8" fill="none"/></svg>Lorem ipsum dolor</div>
    <div><svg width="14" height="14" viewBox="0 0 16 16"><circle cx="8" cy="8" r="8" fill="#222"/><path d="M5 8h6M8 5l3 3-3 3" stroke="#fff" stroke-width="1.8" fill="none"/></svg>Lorem ipsum dolor</div>
    <div><svg width="14" height="14" viewBox="0 0 16 16"><circle cx="8" cy="8" r="8" fill="#222"/><path d="M5 8h6M8 5l3 3-3 3" stroke="#fff" stroke-width="1.8" fill="none"/></svg>Lorem ipsum dolor</div>
    <div><svg width="14" height="14" viewBox="0 0 16 16"><circle cx="8" cy="8" r="8" fill="#222"/><path d="M5 8h6M8 5l3 3-3 3" stroke="#fff" stroke-width="1.8" fill="none"/></svg>Lorem ipsum dolor</div>
    <div><svg width="14" height="14" viewBox="0 0 16 16"><circle cx="8" cy="8" r="8" fill="#222"/><path d="M5 8h6M8 5l3 3-3 3" stroke="#fff" stroke-width="1.8" fill="none"/></svg>Lorem ipsum dolor</div>
  </div>
  <div class="abs btn loc-btn">View More</div>
</section>

<section>
  <div class="abs contact" role="img" aria-label="Outdoor air conditioning units under a red tint"></div>
  <div class="abs center display con-kicker">Contact Us</div>
  <div class="abs center display con-title">Request a Service Call</div>
  <div class="abs field" style="top:3467px;left:208px;width:384px;height:53px">First Name</div>
  <div class="abs field" style="top:3467px;left:606px;width:385px;height:53px">Last Name</div>
  <div class="abs field" style="top:3536px;left:208px;width:384px;height:53px">Email</div>
  <div class="abs field" style="top:3536px;left:606px;width:385px;height:53px">Phone Number</div>
  <div class="abs field msg" style="top:3605px;left:208px;width:783px;height:99px">Message</div>
  <div class="abs submit">Submit</div>
</section>

<footer>
  <div class="abs" style="top:3905px;left:103px;display:flex;align-items:center;gap:10px">
    <div style="width:18px;height:18px;background:var(--red)"></div>
    <div class="brand" style="font-size:24px">Coastal Breeze<br><span style="font-size:17px">Cooling Company</span></div>
  </div>

  <div class="abs" style="top:3894px;left:368px">
    <div class="foot-h">Quick Links</div>
    <div class="foot-links" style="margin-top:16px">Home<br>About Us<br>Our Services<br>Testimonials<br>Contact Us<br>Request Service</div>
  </div>

  <div class="abs" style="top:3894px;left:535px">
    <div class="foot-h">Contact Details</div>
    <div class="contact-item" style="margin-top:20px"><div class="ic-navy"><svg width="12" height="14" viewBox="0 0 12 16" fill="#fff"><path d="M6 0a6 6 0 0 0-6 6c0 4.5 6 10 6 10s6-5.5 6-10a6 6 0 0 0-6-6zm0 8.5A2.5 2.5 0 1 1 6 3.5a2.5 2.5 0 0 1 0 5z"/></svg></div>Address :</div>
    <div class="foot-small" style="margin-top:4px">258, Coastal Breeze<br>Cooling Company</div>
    <div class="contact-item" style="margin-top:14px"><div class="ic-navy"><svg width="13" height="13" viewBox="0 0 24 24" fill="#fff"><path d="M6.6 10.8a15 15 0 0 0 6.6 6.6l2.2-2.2c.3-.3.7-.4 1-.2 1.1.4 2.3.6 3.6.6.6 0 1 .4 1 1V20c0 .6-.4 1-1 1A17 17 0 0 1 3 4c0-.6.4-1 1-1h3.5c.6 0 1 .4 1 1 0 1.3.2 2.5.6 3.6.1.3 0 .7-.2 1z"/></svg></div>Telephone :</div>
    <div class="foot-small" style="margin-top:4px">+1 813 555 0142</div>
    <div class="contact-item" style="margin-top:20px"><div class="ic-navy"><svg width="13" height="11" viewBox="0 0 16 12" fill="none" stroke="#fff" stroke-width="1.6"><rect x="1" y="1" width="14" height="10"/><path d="M1 1l7 6 7-6"/></svg></div>E - mail :</div>
    <div class="foot-small" style="margin-top:4px">info@coastalbreezecooling.example</div>
  </div>

  <div class="abs" style="top:3894px;left:824px;width:251px">
    <div class="foot-h">Newsletter</div>
    <div class="foot-small" style="margin-top:20px;font-size:12px;line-height:20px">Lorem ipsum dolor sit amet, consectetur adipiscing elit, sed do</div>
    <div style="margin-top:18px;height:32px;border:1px solid #ddd;display:flex;align-items:center;gap:5px;padding-left:10px;font-family:'Poppins',sans-serif;font-size:12px;color:#333">
      <svg width="12" height="9" viewBox="0 0 16 12" fill="#333"><path d="M0 0h16v2L8 7 0 2zM0 4l8 5 8-5v8H0z"/></svg>Enter Email
    </div>
    <div class="display" style="margin-top:8px;height:34px;line-height:34px;background:var(--red);color:#fff;text-align:center;font-size:12px">Subscribe</div>
  </div>

  <div class="abs center copy">©Copyrights 2024 <a>The Coastal Breeze Cooling Company</a> | All Rights Reserved</div>
</footer>

</body>
</html>
```